Corvel Capital LLC

Need Professional Business cards for New Investment Fund

Target Market(s)

High Quality investors

Industry/Entity Type

Financial

Contact Information for Business Card

Phone Number +1 555 284 6190
Name Lukas Varenko
Title Fund Manager
email lv@FundCorvel.com
Website www.FundCorvel.com

Colors

Designer to choose colors to be used in the design.

Requirements
Must have
• Must have our Logo and all of the above. Must be made so lettering and loge can be raised

```html
<!DOCTYPE html>
<html lang="en">
<head>
<meta charset="utf-8">
<title>Orvandel — Business Card</title>
<link rel="stylesheet" href="https://fonts.googleapis.com/css2?family=Heebo:wght@400;500;700&display=swap">
<style>
  :root {
    --green: #5dbb46;
    --charcoal: #3c4238;
    --white: #ffffff;
    --backdrop: #3a3b3d;
    --ink: #2c2c2c;
  }
  html, body {
    margin: 0;
    padding: 0;
    overflow: hidden;
  }
  body {
    width: 1200px;
    height: 900px;
    background: var(--backdrop);
    position: relative;
    font-family: "Heebo", Arial, sans-serif;
  }
  .card {
    position: absolute;
    width: 520px;
    height: 300px;
    border-radius: 22px;
    overflow: hidden;
  }
  .card-front {
    left: 90px;
    top: 140px;
    background: var(--green);
    display: flex;
    align-items: center;
    justify-content: center;
  }
  .card-back {
    left: 590px;
    top: 470px;
    background: var(--white);
  }
  .wordmark {
    font-weight: 700;
    letter-spacing: 3px;
    text-transform: uppercase;
    display: flex;
    align-items: center;
    gap: 12px;
    white-space: nowrap;
  }
  .wordmark-mark {
    width: 14px;
    height: 14px;
  }
  .card-front .wordmark {
    color: var(--white);
    font-size: 36px;
  }
  .card-front .wordmark-mark {
    background: var(--white);
  }
  .card-back .wordmark {
    position: absolute;
    left: 36px;
    top: 108px;
    color: var(--green);
    font-size: 26px;
  }
  .card-back .wordmark-mark {
    background: var(--green);
  }
  .wave {
    position: absolute;
    inset: 0;
    width: 100%;
    height: 100%;
  }
  .identity {
    position: absolute;
    right: 36px;
    top: 30px;
    text-align: right;
  }
  .identity-name {
    color: var(--green);
    font-size: 22px;
    font-weight: 500;
    line-height: 1.1;
  }
  .identity-title {
    color: var(--ink);
    font-size: 14px;
    line-height: 1.4;
  }
  .contacts {
    position: absolute;
    right: 22px;
    top: 140px;
    margin: 0;
    padding: 0;
    list-style: none;
  }
  .contact-item {
    display: flex;
    align-items: center;
    justify-content: flex-end;
    gap: 10px;
    color: var(--white);
    font-size: 16px;
    height: 30px;
  }
  .contact-icon {
    width: 18px;
    height: 18px;
    flex: none;
  }
</style>
</head>
<body>
  <section class="card card-front" aria-label="Card front">
    <div class="wordmark"><span class="wordmark-mark"></span>Orvandel</div>
  </section>

  <section class="card card-back" aria-label="Card back">
    <svg class="wave" viewBox="0 0 520 300" aria-hidden="true">
      <path fill="var(--green)" d="M0 258 C120 252 230 240 300 178 C360 125 430 112 520 106 L520 300 L0 300 Z"/>
      <path fill="var(--charcoal)" d="M18 236 C120 214 236 206 318 142 C262 200 140 228 18 250 Z"/>
    </svg>

    <div class="wordmark"><span class="wordmark-mark"></span>Orvandel</div>

    <div class="identity">
      <div class="identity-name">Lukas Varenko</div>
      <div class="identity-title">Fund Manager</div>
    </div>

    <ul class="contacts">
      <li class="contact-item">+1 555 284 6190
        <svg class="contact-icon" viewBox="0 0 24 24" aria-hidden="true"><path fill="var(--white)" d="M6.6 10.8a15.1 15.1 0 0 0 6.6 6.6l2.2-2.2c.3-.3.7-.4 1-.2 1.1.4 2.3.6 3.6.6.6 0 1 .4 1 1V20c0 .6-.4 1-1 1A17 17 0 0 1 3 4c0-.6.4-1 1-1h3.5c.6 0 1 .4 1 1 0 1.3.2 2.5.6 3.6.1.3 0 .7-.2 1z"/></svg>
      </li>
      <li class="contact-item">lv@FundCorvel.com
        <svg class="contact-icon" viewBox="0 0 24 24" aria-hidden="true"><path fill="var(--white)" d="M2 5h20v14H2z"/><path fill="none" stroke="var(--green)" stroke-width="1.6" d="M2.5 5.5 12 13l9.5-7.5"/></svg>
      </li>
      <li class="contact-item">www.FundCorvel.com
        <svg class="contact-icon" viewBox="0 0 24 24" aria-hidden="true"><circle cx="12" cy="12" r="10" fill="var(--white)"/><path fill="none" stroke="var(--green)" stroke-width="1.5" d="M2 12h20M12 2c3 3 3 17 0 20M12 2c-3 3-3 17 0 20"/></svg>
      </li>
    </ul>
  </section>
</body>
</html>
```